A6 Flyers for sports betting / sports advisory service

WE are looking for flyer design for our business to promote a new promo. The flyer must be in similar colours to our website www.kestrelvane.com.au.

the flyer must contain a small intro to who we are and what we do as well as details of how to subscribe to our website etc. It must be eye catching as these will be given out to potential customers as sporting events etc

Target Market(s)

Sports Bettors / Gamblers

Industry/Entity Type

Gambling

Font styles to use
Serif

Requirements
Must have
• Catchy look and layout in colours similar to our website
Nice to have
• scan code
Should not have
• None

```html
<!DOCTYPE html>
<html lang="en">
<head>
<meta charset="utf-8">
<title>Kestrel Vane – Flyer</title>
<link rel="stylesheet" href="https://fonts.googleapis.com/css2?family=Montserrat:wght@700&family=Roboto:wght@300;400&display=swap">
<style>
  :root {
    --ink: #050505;
    --white: #ffffff;
    --text: #e6e6e6;
    --lime: #7a9a0c;
    --lime-bright: #7fa10f;
    --olive: #5f7a05;
    --olive-mid: #6b8a02;
    --charcoal: #1a1a1a;
    --figure: #2a2a2a;
  }
  * { margin: 0; padding: 0; box-sizing: border-box; }
  html, body { width: 848px; height: 1200px; overflow: hidden; background: var(--ink); }
  .flyer {
    position: relative;
    width: 848px;
    height: 1200px;
    background: var(--ink);
    overflow: hidden;
    font-family: "Roboto", Arial, sans-serif;
    font-weight: 300;
    color: var(--text);
  }
  .top-bar {
    position: absolute; left: 0; top: 0;
    width: 100%; height: 14px;
    background: var(--lime);
  }
  .hero-figure {
    position: absolute; left: 430px; top: 240px;
    width: 418px; height: 640px;
  }
  .waves {
    position: absolute; left: 0; top: 0;
    width: 848px; height: 1200px;
  }
  .content {
    position: absolute; left: 82px; top: 176px;
    width: 650px;
  }
  .brand {
    font-family: "Montserrat", Arial, sans-serif;
    font-weight: 700;
    font-size: 42px;
    line-height: 1.05;
    color: var(--white);
    letter-spacing: 0.5px;
  }
  .tagline {
    font-family: "Montserrat", Arial, sans-serif;
    font-weight: 700;
    font-size: 55px;
    line-height: 1.1;
    color: var(--lime-bright);
    margin-top: 2px;
  }
  .copy {
    font-size: 19px;
    line-height: 1.35;
    margin-top: 48px;
  }
  .copy p + p { margin-top: 26px; }
  .web-link {
    display: block;
    font-family: "Roboto", Arial, sans-serif;
    font-weight: 400;
    font-size: 29px;
    line-height: 1.2;
    color: var(--lime-bright);
    margin-top: 4px;
  }
  .price {
    font-weight: 400;
    font-size: 29px;
    color: var(--lime-bright);
  }
  .rule {
    position: absolute; left: 82px;
    width: 194px; height: 3px;
    background: var(--white);
  }
  .rule--upper { top: 757px; }
  .rule--lower { top: 1128px; }
  .footer-link {
    position: absolute; left: 82px; top: 1070px;
    font-family: "Roboto", Arial, sans-serif;
    font-weight: 400;
    font-size: 31px;
    color: var(--lime-bright);
  }
</style>
</head>
<body>
<div class="flyer">
  <div class="top-bar"></div>

  <svg class="hero-figure" role="img" aria-label="Silhouette of a cheering sports fan with arms raised" viewBox="0 0 418 640" preserveAspectRatio="none">
    <defs>
      <radialGradient id="figureGlow" cx="50%" cy="45%" r="55%">
        <stop offset="0%" stop-color="#2a2a2a"/>
        <stop offset="70%" stop-color="#1a1a1a"/>
        <stop offset="100%" stop-color="#050505"/>
      </radialGradient>
    </defs>
    <rect width="418" height="640" fill="url(#figureGlow)"/>
  </svg>

  <svg class="waves" viewBox="0 0 620 877" preserveAspectRatio="none" aria-hidden="true">
    <path d="M190 690 C330 600 480 570 620 572 L620 877 L190 877 Z" fill="#7a9a0c"/>
    <path d="M250 682 C380 622 500 600 620 605 L620 877 L250 877 Z" fill="#5f7a05"/>
    <path d="M290 692 C400 645 520 632 620 640 L620 877 L290 877 Z" fill="#6b8a02"/>
    <path d="M0 685 C180 660 400 720 620 835 L620 877 L0 877 Z" fill="#1a1a1a"/>
    <path d="M0 706 C200 690 420 760 620 877 L0 877 Z" fill="#050505"/>
  </svg>

  <div class="content">
    <h1 class="brand">KESTREL VANE</h1>
    <h2 class="tagline">YOUR BEST BET YET!</h2>
    <div class="copy">
      <p>We operate a subscription based service which aims to provide profitable sports picks for our customers. We are averaging a 64% win ratio across our two systems for our punters!</p>
      <p>Get online at
        <span class="web-link">www.kestrelvane.com.au</span>
        or like us on Chatterbox<br>“Kestrel Vane” and see for yourself!</p>
      <p style="margin-top:40px">We are currently offering a one off <span class="price">$70 per month</span> fee with no lock in and no minimum period – cancel anytime! We guarantee that you will stick around once you trial our service!</p>
      <p>We will leave it to the designer to alter the content, the above isnt all necessary, we will leave it to you to chop and change as required.</p>
    </div>
  </div>

  <div class="rule rule--upper"></div>
  <div class="footer-link">www.kestrelvane.com.au</div>
  <div class="rule rule--lower"></div>
</div>
</body>
</html>
```